We need a business card design for a new company located in Brampton Ontario Canada. Our goal is to promote companies to use our service as an "External Program Management " firm taking their industrial product concepts " from prototype to production." We would like to use blue and yellow as our colors. Our skills include finding suppliers for prototype parts and developing them into supplying not only prototypes but the final production parts as well for our customer base.
Industry/Entity Type
Business
Contact Information for Business Card
Derek Namsby
Sales Manager
KOLVEN Solutions Inc.
14 Pinemarsh Lane
Brampton, Ontario L7P 2K9
Canada
Phone: 905-481-2976
Fax: 905-481-2976
website: www.kolvensolutions-example.com
Email: derek@kolvensolutions-example.com
Look and feel
Each slider illustrates characteristics of the customer's brand and the style your logo design should communicate.

```html
<!DOCTYPE html>
<html lang="en">
<head>
<meta charset="utf-8">
<title>KOLVEN Solutions Inc. – Business Card</title>
<link href="https://fonts.googleapis.com/css2?family=Exo+2:wght@400;500;700;800&display=swap" rel="stylesheet">
<style>
  :root {
    --backdrop: #e4e4e6;
    --card: #fbfbfc;
    --brand-blue: #1414d8;
    --brand-yellow: #f4c21a;
    --text-dark: #2e2e33;
    --icon-glyph: #ffffff;
  }
  * { margin: 0; padding: 0; box-sizing: border-box; }
  html, body {
    width: 1200px; height: 900px; overflow: hidden;
    background: var(--backdrop);
    font-family: "Exo 2", sans-serif;
  }
  .canvas {
    position: relative; width: 1200px; height: 900px;
    display: flex; align-items: center; justify-content: center;
  }
  .business-card {
    position: relative; width: 1050px; height: 600px;
    background: var(--card);
    overflow: hidden;
    box-shadow: 0 6px 24px rgba(0,0,0,0.12);
  }
  .card-bands { position: absolute; inset: 0; width: 100%; height: 100%; }
  .band-blue { fill: var(--brand-blue); }
  .band-yellow { fill: var(--brand-yellow); }

  .company-name {
    position: absolute; left: 70px; top: 235px;
    color: var(--brand-blue); font-weight: 800; line-height: 0.95;
  }
  .company-name .name-main { display: block; font-size: 112px; letter-spacing: 2px; }
  .company-name .name-sub { display: block; font-size: 50px; letter-spacing: 1px; }

  .contact-list {
    position: absolute; left: 80px; top: 420px;
    list-style: none;
  }
  .contact-item {
    display: flex; align-items: center; gap: 12px;
    font-size: 20px; color: var(--text-dark); height: 30px;
    letter-spacing: 0.5px;
  }
  .contact-icon { width: 22px; height: 22px; flex: none; }
  .contact-icon .icon-disc { fill: var(--brand-blue); }
  .contact-icon .icon-glyph { fill: var(--icon-glyph); }
  .contact-icon .icon-stroke { fill: none; stroke: var(--icon-glyph); stroke-width: 1.4; }

  .person {
    position: absolute; right: 60px; top: 440px; text-align: right;
  }
  .person-name {
    font-size: 30px; font-weight: 500; color: var(--text-dark);
    letter-spacing: 2px; text-transform: uppercase;
  }
  .person-title {
    font-size: 20px; color: var(--brand-blue); letter-spacing: 0.5px;
  }
</style>
</head>
<body>
<main class="canvas">
  <article class="business-card">
    <svg class="card-bands" viewBox="0 0 1050 600" preserveAspectRatio="none" aria-hidden="true">
      <path class="band-yellow" d="M0 0 H1050 V415 C820 330 380 150 0 130 Z"/>
      <path class="band-blue" d="M0 0 H1050 V325 C820 250 380 100 0 90 Z"/>
    </svg>

    <h1 class="company-name">
      <span class="name-main">KOLVEN</span>
      <span class="name-sub">Solutions Inc.</span>
    </h1>

    <ul class="contact-list">
      <li class="contact-item">
        <svg class="contact-icon" viewBox="0 0 22 22" aria-hidden="true">
          <circle class="icon-disc" cx="11" cy="11" r="11"/>
          <path class="icon-glyph" d="M7 6 L9 6 L10 9 L8.6 10 C9.4 11.7 10.4 12.7 12 13.4 L13 12 L16 13 L16 15 C16 15.6 15.5 16 15 16 C10.2 15.6 6.4 11.8 6 7 C6 6.5 6.4 6 7 6 Z"/>
        </svg>
        <span>905-481-2976</span>
      </li>
      <li class="contact-item">
        <svg class="contact-icon" viewBox="0 0 22 22" aria-hidden="true">
          <circle class="icon-disc" cx="11" cy="11" r="11"/>
          <rect class="icon-stroke" x="8" y="5.5" width="6" height="11" rx="1"/>
          <circle class="icon-glyph" cx="11" cy="14.5" r="0.8"/>
        </svg>
        <span>905-481-2976</span>
      </li>
      <li class="contact-item">
        <svg class="contact-icon" viewBox="0 0 22 22" aria-hidden="true">
          <circle class="icon-disc" cx="11" cy="11" r="11"/>
          <rect class="icon-stroke" x="5.5" y="7" width="11" height="8"/>
          <path class="icon-stroke" d="M5.5 7 L11 11.5 L16.5 7"/>
        </svg>
        <span>derek@kolvensolutions-example.com</span>
      </li>
      <li class="contact-item">
        <svg class="contact-icon" viewBox="0 0 22 22" aria-hidden="true">
          <circle class="icon-disc" cx="11" cy="11" r="11"/>
          <circle class="icon-stroke" cx="11" cy="11" r="5.5"/>
          <ellipse class="icon-stroke" cx="11" cy="11" rx="2.4" ry="5.5"/>
          <path class="icon-stroke" d="M5.5 11 H16.5"/>
        </svg>
        <span>www.kolvensolutions-example.com</span>
      </li>
      <li class="contact-item">
        <svg class="contact-icon" viewBox="0 0 22 22" aria-hidden="true">
          <circle class="icon-disc" cx="11" cy="11" r="11"/>
          <path class="icon-glyph" d="M11 5 C8.5 5 7 6.8 7 8.8 C7 11.6 11 17 11 17 C11 17 15 11.6 15 8.8 C15 6.8 13.5 5 11 5 Z"/>
          <circle class="icon-disc" cx="11" cy="8.8" r="1.5"/>
        </svg>
        <span>14 Pinemarsh Lane, Brampton L7P 2K9</span>
      </li>
    </ul>

    <div class="person">
      <p class="person-name">Derek Namsby</p>
      <p class="person-title">Sales Manager</p>
    </div>
  </article>
</main>
</body>
</html>
```